Business Card Update, need to bring life to the card, two sided color

We need a new business card design, are moving and changing addresses and need a new look, we have the logos already attached but need a new style moving forward. Can incorporate the color of the logo (The Green) as well, maybe a solid back? We deal with safety products revolving around static electricity and safety lighting. Would like to keep same font in second logo as well.

Target Market(s)

Electrical Safety, Lighting

Contact Information for Business Card

Dale Fenwick
Vice President
Office: 770-555-4821
Cell: 770-555-3067
dale@tkfenwick.example
www.tkfenwick.example
4700 West Harbor Boulevard
Suite #150
Roswell, GA 30076

Font styles to use
Serif
Sans Serif

Requirements
Must have
• Since 1918
Nice to have
• Could use the 100 Year Logo for back of card, would like the back of card to be the same green as logo.
Should not have
• No black cards please.

```html
<!DOCTYPE html>
<html lang="en">
<head>
<meta charset="utf-8">
<title>T.K. Fenwick Business Card</title>
<link href="https://fonts.googleapis.com/css2?family=Arimo:wght@700&family=Lato:wght@400;700&display=swap" rel="stylesheet">
<style>
  :root {
    --brand-green: #009a5b;
    --backdrop: #a3a3a3;
    --card-white: #ffffff;
    --ink: #1e1e1e;
    --divider: #c9c9c9;
  }
  * { margin: 0; padding: 0; box-sizing: border-box; }
  html, body { width: 1200px; height: 802px; overflow: hidden; }
  body { background: var(--backdrop); position: relative; font-family: "Lato", sans-serif; }

  .card {
    position: absolute;
    top: 274px;
    width: 443px;
    height: 265px;
    box-shadow: 2px 3px 6px rgba(0,0,0,0.35);
  }
  .card-front { left: 136px; background: var(--card-white); }
  .card-back { left: 624px; background: var(--brand-green); }

  .brand-mark {
    position: absolute;
    left: 89px; top: 79px;
    width: 64px; height: 64px;
    border-radius: 50%;
    background: var(--brand-green);
  }
  .brand-name {
    position: absolute;
    left: 0; width: 242px;
    text-align: center;
    font-family: "Arimo", sans-serif;
    font-weight: 700;
    color: var(--brand-green);
  }
  .brand-name.primary { top: 153px; font-size: 21px; }
  .brand-name.secondary { top: 178px; font-size: 10.5px; letter-spacing: 0.5px; }

  .divider {
    position: absolute;
    left: 231px; top: 67px;
    width: 1px; height: 132px;
    background: var(--divider);
  }

  .contact {
    position: absolute;
    left: 246px; top: 66px;
    color: var(--ink);
    font-size: 12.5px;
    line-height: 16px;
  }
  .contact .person-name {
    color: var(--brand-green);
    font-weight: 700;
    font-size: 15.5px;
    letter-spacing: 0.3px;
    line-height: 18px;
  }
  .contact .person-title { font-size: 13px; margin-bottom: 5px; }
  .contact-row { display: flex; align-items: center; gap: 4px; }
  .contact-row svg { width: 10px; height: 10px; flex: none; }
  .address { margin-top: 5px; }

  .back-name {
    position: absolute;
    left: 0; width: 100%;
    text-align: center;
    font-family: "Arimo", sans-serif;
    font-weight: 700;
    color: var(--card-white);
  }
  .back-name.primary { top: 102px; font-size: 34px; }
  .back-name.secondary { top: 141px; font-size: 16.5px; letter-spacing: 0.8px; }
  .back-name.since { top: 170px; font-size: 12px; letter-spacing: 1.5px; text-transform: uppercase; }
</style>
</head>
<body>
  <section class="card card-front">
    <div class="brand-mark"></div>
    <div class="brand-name primary">T.K. Fenwick</div>
    <div class="brand-name secondary">Manufacturing Company, Inc.</div>
    <div class="divider"></div>
    <div class="contact">
      <div class="person-name">DALE FENWICK</div>
      <div class="person-title">Vice President</div>
      <div class="contact-row">
        <svg viewBox="0 0 10 10"><path d="M1 4 Q5 0 9 4 L8 5 L6.5 4 L6.5 3 Q5 2.5 3.5 3 L3.5 4 L2 5 Z M2.5 5.5 H7.5 L8.5 9 H1.5 Z" fill="var(--brand-green)"/></svg>
        <span>770-555-4821</span>
      </div>
      <div class="contact-row">
        <svg viewBox="0 0 10 10"><rect x="2.5" y="0.5" width="5" height="9" rx="1" fill="none" stroke="var(--brand-green)" stroke-width="1.2"/></svg>
        <span>770-555-3067</span>
      </div>
      <div class="contact-row">
        <svg viewBox="0 0 10 10"><rect x="0.5" y="2" width="9" height="6.5" fill="var(--brand-green)"/><path d="M0.8 2.3 L5 5.6 L9.2 2.3" fill="none" stroke="#fff" stroke-width="0.9"/></svg>
        <span>dale@tkfenwick.example</span>
      </div>
      <div class="contact-row">
        <svg viewBox="0 0 10 10"><circle cx="5" cy="5" r="4.5" fill="var(--brand-green)"/><path d="M3 3.5 Q5 3 5.5 5 Q6 7 4 7.5" fill="none" stroke="#fff" stroke-width="0.9"/></svg>
        <span>www.tkfenwick.example</span>
      </div>
      <div class="address">4700 West Harbor Boulevard<br>Roswell, GA 30076</div>
    </div>
  </section>

  <section class="card card-back">
    <div class="back-name primary">T.K. Fenwick</div>
    <div class="back-name secondary">Manufacturing Company, Inc.</div>
    <div class="back-name since">Since 1918</div>
  </section>
</body>
</html>
```